Locksmith Business Cards

My father-in-law is in need of new business cards for his locksmith business and I need to impress him. Kindly help me out!

You can see the previous business card attached. It is a family run business in North Wales.

No individual names on the cards.

Key Things to Feature:
- The words "Prompt", "Local", "Reliable" (as you can see under the logo on the website)
- 24h Emergency Service
- Covering All of North Wales, the Wirral and Chester
- The color blue
- A key or a lock would be interesting (similar to the ones that come up when you google locksmith business card)

Optional (only if design includes bullet points, like the example below):
https://imgvaultcdn.net/samples/208314/55172/55172_3904821_208314_image.jpg
- Residential / Commercial / Automotive
- Alarms & Cameras
- Key Cutting & Safes

https://www.brynhafod-locksmiths.co.uk/

Industry/Entity Type

Locksmith

Contact Information for Business Card

01632 960 418
07700 900 362
brynhafodlocksmiths@mailvane.com
Brynhafod Locksmiths, The Willow Barn, 7 Tannery Rd., Llandudno LL99 4QX
www.brynhafod-locksmiths.co.uk

Requirements
Must have
• - The words "Prompt", "Local", "Reliable" (as you can see under the logo on the website)
• - 24h Emergency Service
• - Covering All of North Wales, the Wirral and Chester
Nice to have
• - A key or a lock would be interesting (similar to the ones that come up when you google locksmith business card)

```html
<!DOCTYPE html>
<html lang="en">
<head>
<meta charset="utf-8">
<title>Brynhafod Locksmiths – Business Cards</title>
<link href="https://fonts.googleapis.com/css2?family=Oswald:wght@500&family=Roboto:wght@400&display=swap" rel="stylesheet">
<style>
  :root {
    --backdrop: #3a3a3a;
    --card-dark: #1c1c1c;
    --card-light: #ffffff;
    --brand-blue: #34418f;
    --text-dark: #3a3a3a;
    --text-light: #f2f2f2;
    --mark-grey: #8c8c8c;
  }
  * { box-sizing: border-box; margin: 0; padding: 0; }
  html, body {
    width: 1200px; height: 900px; overflow: hidden;
    background: var(--backdrop);
    font-family: "Roboto", Arial, sans-serif;
  }
  .sheet {
    position: relative; width: 1200px; height: 900px;
    display: flex; flex-direction: column; align-items: center;
    justify-content: center; gap: 40px;
  }
  .card {
    position: relative; width: 640px; height: 390px;
    box-shadow: 0 10px 30px rgba(0,0,0,.45);
  }

  /* Front (dark) */
  .card--front {
    background: var(--card-dark); color: var(--text-light);
    display: flex; flex-direction: column; align-items: center; justify-content: center;
  }
  .brand { display: flex; align-items: center; gap: 16px; }
  .brand__badge { flex: none; border-radius: 12px; }
  .brand__name {
    font-family: "Oswald", "Arial Narrow", sans-serif; font-weight: 500;
    text-transform: uppercase; line-height: .98; letter-spacing: .5px;
  }
  .card--front .brand__badge { width: 78px; height: 78px; background: #2a2a2a; }
  .card--front .brand__name { font-size: 44px; color: var(--mark-grey); }
  .taglines { margin-top: 26px; text-align: center; font-size: 17px; line-height: 1.3; letter-spacing: .3px; }

  /* Back (light) */
  .card--back { background: var(--card-light); color: var(--text-dark); padding: 34px 40px; }
  .card--back .brand__badge { width: 54px; height: 54px; background: var(--brand-blue); border-radius: 9px; }
  .card--back .brand { gap: 10px; }
  .card--back .brand__name { font-size: 29px; color: var(--brand-blue); }
  .services { margin-top: 12px; font-size: 16px; line-height: 1.3; }
  .divider {
    position: absolute; left: 40px; width: 380px; top: 212px;
    height: 1.5px; background: var(--brand-blue);
  }
  .contacts { position: absolute; left: 40px; top: 234px; list-style: none; font-size: 19px; line-height: 1.4; }
  .contacts li { display: flex; align-items: center; gap: 8px; }
  .contacts svg { width: 17px; height: 17px; fill: var(--brand-blue); flex: none; }
  .address {
    position: absolute; right: 34px; top: 187px; text-align: right;
    font-size: 18px; line-height: 1.35; color: var(--brand-blue); font-style: normal;
  }
</style>
</head>
<body>
<main class="sheet">
  <section class="card card--front">
    <div class="brand">
      <span class="brand__badge"></span>
      <div class="brand__name">Brynhafod<br>Locksmiths</div>
    </div>
    <p class="taglines">PROMPT - LOCAL - RELIABLE<br>24h Emergency Service<br>Covering All of North Wales, the Wirral and Chester</p>
  </section>

  <section class="card card--back">
    <div class="brand">
      <span class="brand__badge"></span>
      <div class="brand__name">Brynhafod<br>Locksmiths</div>
    </div>
    <p class="services">Residential | Commercial | Automotive<br>Alarms &amp; Cameras<br>Key Cutting &amp; Safes</p>
    <div class="divider"></div>
    <ul class="contacts">
      <li><svg viewBox="0 0 24 24"><path d="M6.6 10.8a15 15 0 0 0 6.6 6.6l2.2-2.2a1 1 0 0 1 1-.25 11.4 11.4 0 0 0 3.6.57 1 1 0 0 1 1 1V20a1 1 0 0 1-1 1A17 17 0 0 1 3 4a1 1 0 0 1 1-1h3.5a1 1 0 0 1 1 1c0 1.25.2 2.45.57 3.57a1 1 0 0 1-.25 1z"/></svg>01632 960 418</li>
      <li><svg viewBox="0 0 24 24"><path d="M6.6 10.8a15 15 0 0 0 6.6 6.6l2.2-2.2a1 1 0 0 1 1-.25 11.4 11.4 0 0 0 3.6.57 1 1 0 0 1 1 1V20a1 1 0 0 1-1 1A17 17 0 0 1 3 4a1 1 0 0 1 1-1h3.5a1 1 0 0 1 1 1c0 1.25.2 2.45.57 3.57a1 1 0 0 1-.25 1z"/></svg>07700 900 362</li>
      <li><svg viewBox="0 0 24 24"><path d="M2 5h20v14H2z M3 6l9 7 9-7" fill="none" stroke="#34418f" stroke-width="2"/><path d="M2 5h20l-10 8z"/></svg>brynhafodlocksmiths@mailvane.com</li>
      <li><svg viewBox="0 0 24 24"><circle cx="12" cy="12" r="10" fill="none" stroke="#34418f" stroke-width="2"/><path d="M2 12h20M12 2c3 3 3 17 0 20M12 2c-3 3-3 17 0 20" fill="none" stroke="#34418f" stroke-width="1.6"/></svg>www.brynhafod-locksmiths.co.uk</li>
    </ul>
    <address class="address">The Willow Barn, 7 Tannery Rd.<br>Llandudno LL99 4QX</address>
  </section>
</main>
</body>
</html>
```